Lucky Harbour Fun Casino Entertainment

Looking to update my business card and make it look more modern, stand out and eye catching.
We are are fun casino business in Australia (primarily Sydney). Blackjack and Roulette are our most popular games although we have pretty much every game available for hire that you would find in a real casino. The final design would need to be sleek and appeal to the more upmarket corporate sector.
We mainly cater for Corporate Events, Private Parties, Fundraising Events, Team Building, Poker Tournaments
I think I'd prefer the colour Black.

Target Market(s)

High-end Corporate

Industry/Entity Type

Events

Contact Information for Business Card

Rob Kendall
Director
1300 482 617
0433 728 591
info@luckyharbour.com.au
www.luckyharbour.com.au
Facebook & Instagram @luckyharbourevents (proper social icons preferred)

Colors
000000
0255a3

Requirements
Must have
• Front side:
• Logo
• Contact details
• 'Australia's #1 Fun Casino Specialists'
• Back:
• Logo
Nice to have
• Back:
• Corporate Events
• Private Parties
• Poker Tournaments
• Fundraising
• Props & Theming
• Photo Booth
• Horse Racing Events
• The Vegas Sign attached, maybe on the back of the card in the background...?

```html
<!DOCTYPE html>
<html lang="en">
<head>
<meta charset="utf-8">
<title>Lucky Harbour Fun Casino Entertainment – Business Card</title>
<link href="https://fonts.googleapis.com/css2?family=Questrial&display=swap" rel="stylesheet">
<style>
:root{
  --bg:#1b1b1d;
  --card:#050505;
  --gold:#f6b21b;
  --gold-deep:#e89a0c;
  --white:#f4f4f4;
  --blue:#0255a3;
  --grey:#2a2a2c;
}
*{margin:0;padding:0;box-sizing:border-box}
html,body{width:1200px;height:800px;overflow:hidden;background:var(--bg);font-family:"Questrial",sans-serif}
.stage{width:1200px;height:800px;display:flex;align-items:center;justify-content:center;gap:30px}
.card{position:relative;width:560px;height:320px;border-radius:18px;overflow:hidden;background:var(--card);box-shadow:0 10px 30px rgba(0,0,0,.5)}

/* brand name block */
.brand{position:absolute;display:flex;align-items:center;gap:12px}
.brand-dot{border-radius:50%;background:var(--gold);flex:none}
.brand-name{color:var(--gold);font-weight:400;text-transform:uppercase;letter-spacing:1px;line-height:1.05}

/* front */
.front .brand{right:34px;top:36px}
.front .brand-dot{width:58px;height:58px}
.front .brand-name{font-size:28px;width:150px}
.contact{position:absolute;left:40px;top:58px;width:300px}
.person-name{color:var(--gold);font-size:21px;text-transform:uppercase;letter-spacing:.5px;line-height:1.2}
.person-role{color:var(--white);font-size:13px;margin-top:1px}
.rule{height:1.5px;background:var(--gold);margin:7px 0 7px;width:270px}
.line{display:flex;align-items:center;gap:9px;color:var(--white);font-size:13px;height:17px}
.line .accent{color:var(--gold)}
.icon{width:14px;height:14px;flex:none}
.tagline{margin-top:12px;color:var(--gold);font-size:17px;line-height:1.2}

/* back */
.back-photo{position:absolute;inset:0;background:radial-gradient(ellipse at 45% 50%,#5a3a2a 0%,#3a2620 35%,#1a1412 75%)}
.back .brand{right:34px;top:26px;flex-direction:column;align-items:flex-end;gap:10px}
.back .brand-dot{width:110px;height:110px;background:var(--grey);border:13px solid var(--gold)}
.back .brand-name{font-size:32px;text-align:right;width:200px}
.services{position:absolute;left:40px;top:72px}
.services-title{color:var(--gold);font-size:18px;text-transform:uppercase;letter-spacing:1px;margin-bottom:8px}
.service{display:flex;align-items:center;gap:10px;color:var(--white);font-size:15px;height:21px}
.chip{width:14px;height:14px;flex:none}
.band{position:absolute;left:0;bottom:0;width:560px;height:70px}
.url{position:absolute;right:34px;bottom:12px;color:#111;font-size:15px;letter-spacing:1px}
</style>
</head>
<body>
<main class="stage">

  <section class="card front" aria-label="Business card front">
    <div class="brand">
      <span class="brand-dot"></span>
      <span class="brand-name">Lucky Harbour</span>
    </div>

    <div class="contact">
      <p class="person-name">Rob Kendall</p>
      <p class="person-role">Director</p>
      <div class="rule"></div>

      <p class="line">
        <svg class="icon" viewBox="0 0 14 14"><circle cx="7" cy="7" r="7" fill="var(--gold)"/><path d="M4.3 3.6l1.4-.2.7 1.6-.8.7a5 5 0 0 0 2.7 2.7l.7-.8 1.6.7-.2 1.4c-3.4.2-6.3-2.7-6.1-6.1z" fill="#000"/></svg>
        <span>1300 482 617</span>
      </p>
      <p class="line">
        <svg class="icon" viewBox="0 0 14 14"><circle cx="7" cy="7" r="7" fill="var(--gold)"/><rect x="5" y="3" width="4" height="8" rx=".8" fill="#000"/><rect x="5.7" y="4" width="2.6" height="5" fill="var(--gold)"/></svg>
        <span>0433 728 591</span>
      </p>
      <p class="line">
        <svg class="icon" viewBox="0 0 14 14"><circle cx="7" cy="7" r="7" fill="var(--gold)"/><rect x="3.5" y="4.5" width="7" height="5" fill="#000"/><path d="M3.5 4.5L7 7.3l3.5-2.8" stroke="var(--gold)" stroke-width=".8" fill="none"/></svg>
        <span>info@luckyharbour.com.au</span>
      </p>
      <p class="line">
        <svg class="icon" viewBox="0 0 14 14"><circle cx="7" cy="7" r="7" fill="var(--gold)"/><circle cx="7" cy="7" r="3.6" fill="none" stroke="#000" stroke-width=".9"/><path d="M3.4 7h7.2M7 3.4c-1.6 2-1.6 5.2 0 7.2M7 3.4c1.6 2 1.6 5.2 0 7.2" stroke="#000" stroke-width=".8" fill="none"/></svg>
        <span>www.<span class="accent">luckyharbour</span>.com.au</span>
      </p>

      <div class="rule"></div>

      <p class="line">
        <svg class="icon" viewBox="0 0 14 14"><circle cx="7" cy="7" r="7" fill="var(--gold)"/></svg>
        <span>@luckyharbourevents</span>
      </p>
      <p class="line">
        <svg class="icon" viewBox="0 0 14 14"><circle cx="7" cy="7" r="7" fill="var(--gold)"/></svg>
        <span>@luckyharbourevents</span>
      </p>

      <p class="tagline">Australia's #1<br>Fun Casino Specialists</p>
    </div>
  </section>

  <section class="card back" aria-label="Business card back">
    <div class="back-photo" role="img" aria-label="Faint photo of a classic illuminated casino welcome sign"></div>

    <div class="services">
      <p class="services-title">Our Services</p>
      <p class="service"><svg class="chip" viewBox="0 0 14 14"><circle cx="7" cy="7" r="7" fill="var(--blue)"/><circle cx="7" cy="7" r="4.5" fill="none" stroke="#fff" stroke-width="1.4" stroke-dasharray="2 1.6"/></svg>Corporate Events</p>
      <p class="service"><svg class="chip" viewBox="0 0 14 14"><circle cx="7" cy="7" r="7" fill="var(--blue)"/><circle cx="7" cy="7" r="4.5" fill="none" stroke="#fff" stroke-width="1.4" stroke-dasharray="2 1.6"/></svg>Private Parties</p>
      <p class="service"><svg class="chip" viewBox="0 0 14 14"><circle cx="7" cy="7" r="7" fill="var(--blue)"/><circle cx="7" cy="7" r="4.5" fill="none" stroke="#fff" stroke-width="1.4" stroke-dasharray="2 1.6"/></svg>Poker Tournaments</p>
      <p class="service"><svg class="chip" viewBox="0 0 14 14"><circle cx="7" cy="7" r="7" fill="var(--blue)"/><circle cx="7" cy="7" r="4.5" fill="none" stroke="#fff" stroke-width="1.4" stroke-dasharray="2 1.6"/></svg>Fundraising</p>
      <p class="service"><svg class="chip" viewBox="0 0 14 14"><circle cx="7" cy="7" r="7" fill="var(--blue)"/><circle cx="7" cy="7" r="4.5" fill="none" stroke="#fff" stroke-width="1.4" stroke-dasharray="2 1.6"/></svg>Props &amp; Theming</p>
      <p class="service"><svg class="chip" viewBox="0 0 14 14"><circle cx="7" cy="7" r="7" fill="var(--blue)"/><circle cx="7" cy="7" r="4.5" fill="none" stroke="#fff" stroke-width="1.4" stroke-dasharray="2 1.6"/></svg>Photo Booth</p>
      <p class="service"><svg class="chip" viewBox="0 0 14 14"><circle cx="7" cy="7" r="7" fill="var(--blue)"/><circle cx="7" cy="7" r="4.5" fill="none" stroke="#fff" stroke-width="1.4" stroke-dasharray="2 1.6"/></svg>Horse Racing Events</p>
    </div>

    <div class="brand">
      <span class="brand-dot"></span>
      <span class="brand-name">Lucky Harbour</span>
    </div>

    <svg class="band" viewBox="0 0 560 70" preserveAspectRatio="none">
      <polygon points="0,70 0,50 300,50 360,8 560,8 560,70" fill="var(--gold-deep)"/>
      <polygon points="0,70 0,56 306,56 366,14 560,14 560,70" fill="var(--gold)"/>
      <polygon points="0,70 0,46 296,46 356,4 560,4 560,6 358,6 298,48 0,48" fill="var(--gold)"/>
    </svg>
    <p class="url">www.luckyharbour.com.au</p>
  </section>

</main>
</body>
</html>
```